Web design for small empirical brand consulting company that will sell a web-based brand tool

We need a totally new and very appealing website:
Purpose: We want to attract lots of potential customers with this website... especially, we want to sell our web-based tool valuquant®... we want to be perceived as innovative, trendy, but solid and reliable… we want customers go to the website, login at „valuquant®“ (see structure), and perceive how it works.. and the contacting us or in the near future being able to buy a login and work with the tool… so we want to a) inform (on the website or send the url to customers) and b) to „force“ potential customers getting in contact with us…
Structure (e.g.): Must Home, valuquant®, About us, Contact (incl. legal notice); we are open for more, Nice to have e.g. references/clients, press... for example, we publish a nice book in a couple of months and might want to show it somewhere on the website as well...)
Layout: We would like to have more/mainly figures - may be animated or something like that – in specific those on slides 7 and 8 as well as 6 and 9 (which would be for our web-based tool valuquant®...)... excellent, but simple and with few text…
Fonts: Eurostile; CMYK 100/23/100/19, CMYK 0/0/0/70
Logo: Would you please use the lorentavo-logo used in this file?
Social Media: we think that it might make sense to be connected to chatterbay, quipline and so on as well…
Phantasy: May be it is possible to have something between a classic marketing research and an e-commerce website... just a thought... because it is mainly about the new tool that will be assessable through a login... but customers might want to contact us or vice versa in order to check how the tool will work (btw: you do not have further info about valuquant® here... I know)… I dream of having a site where people go to and by components of our tool like at brimbo… click and buy and go for it…
It is possible to program it in php or java? Thanks.
Pages I personally like: Don’t know if that helps, but I personally like those websites just they seem so simple: http:// www.pellivarn.com/, http://www.craftelune.net/... but I am veeery open
Pages I do not like anymore: my own www.lorentavo.ch

```html
<!DOCTYPE html>
<html lang="en">
<head>
<meta charset="utf-8">
<title>lorentavo – empirical brand consulting</title>
<link rel="stylesheet" href="https://fonts.googleapis.com/css2?family=Open+Sans:wght@400;600;700&display=swap">
<style>
:root{
  --green:#0b6a2e;
  --green-dark:#07501f;
  --charcoal:#333333;
  --charcoal-deep:#2b2b2b;
  --card:#262626;
  --text:#555555;
  --muted:#8a8a8a;
  --white:#ffffff;
  --rule:#dddddd;
}
*{margin:0;padding:0;box-sizing:border-box}
html,body{width:1200px;height:3243px;overflow:hidden}
body{font-family:"Open Sans",Arial,sans-serif;color:var(--text);background:var(--white);position:relative}
section,header,footer{position:absolute;left:0;width:1200px}
.abs{position:absolute}

/* header */
.site-header{top:0;height:80px;background:var(--charcoal)}
.logo{left:180px;top:20px;font-size:30px;font-weight:600;color:#cfcfcf;letter-spacing:-0.5px;display:flex;align-items:center;gap:8px}
.logo-mark{width:14px;height:28px;background:var(--green)}
.main-nav{right:180px;top:36px;display:flex;gap:24px;font-size:12px;color:var(--white);text-transform:uppercase;letter-spacing:.3px}
.main-nav .active{border-bottom:2px solid var(--white);padding-bottom:6px}

/* hero */
.hero{top:80px;height:417px;background:linear-gradient(100deg,#2f4540 0%,#4b6a62 45%,#7f9a92 70%,#5a6f6a 100%)}
.hero-photo{inset:0}
.hero-box{left:180px;top:97px;width:354px;height:169px;background:rgba(235,235,235,.9);padding:28px 20px}
.hero-box h1{font-size:19px;font-weight:600;color:#222;line-height:1.3;text-transform:uppercase}
.hero-box p{font-size:10px;color:#666;line-height:1.45;margin-top:12px}

/* welcome */
.welcome{top:497px;height:394px;background:var(--white)}
.section-title{width:100%;text-align:center;font-size:21px;font-weight:600;text-transform:uppercase}
.welcome .section-title{top:40px;color:var(--green)}
.welcome .lead{top:76px;width:100%;text-align:center;font-size:12px;line-height:1.6}
.divider{left:597px;top:163px;width:1px;height:205px;background:var(--rule)}
.checklist{font-size:12px;line-height:1.55;color:#555}
.checklist li{list-style:none;position:absolute;width:340px;padding-left:32px}
.checklist li svg{position:absolute;left:0;top:3px}

/* dark bands */
.services{top:891px;height:568px;background:var(--charcoal)}
.dark .section-title{color:var(--white)}
.dark .lead{width:100%;text-align:center;font-size:12px;line-height:1.6;color:#aaa}
.services .section-title{top:45px}
.services .lead{top:92px}
.service-card{top:183px;width:259px;height:316px;background:var(--card)}
.service-card h3{height:67px;background:var(--green);color:var(--white);font-size:14px;font-weight:400;text-transform:uppercase;padding:24px 20px}
.service-card .card-photo{height:123px;background:linear-gradient(180deg,#c9ced1,#8d959a)}
.service-card p{padding:26px 20px 0;font-size:12px;line-height:1.5;color:#cfcfcf}

/* benefits */
.benefits{top:1459px;height:818px;background:var(--white)}
.benefits .section-title{top:68px;color:var(--green)}
.benefits .lead{top:108px;width:100%;text-align:center;font-size:12px;line-height:1.6;color:var(--muted)}
.benefit{width:200px;text-align:center}
.benefit .badge{width:136px;height:136px;border-radius:50%;background:var(--green);margin:0 auto;display:flex;align-items:center;justify-content:center}
.benefit h4{font-size:15px;font-weight:400;color:var(--green);margin-top:44px;line-height:1.2}
.benefit p{font-size:11px;line-height:1.5;color:var(--muted);margin-top:8px;padding:0 20px}

/* press */
.press{top:2277px;height:573px;background:var(--charcoal)}
.press .section-title{top:52px}
.press .lead{top:100px}
.press-grid{left:210px;top:181px;width:782px;height:312px;display:grid;grid-template-columns:repeat(3,1fr);grid-template-rows:repeat(2,1fr);gap:2px}
.press-tile{position:relative}
.tile-1{background:linear-gradient(135deg,#eeeeee,#b8c4cf)}
.tile-2{background:linear-gradient(135deg,#3a3a3a,#5e5e5e)}
.tile-3{background:linear-gradient(135deg,#1a2f4a,#5f86a8)}
.tile-4{background:linear-gradient(135deg,#8fb4d4,#e2ecf3)}
.tile-5{background:linear-gradient(135deg,#5c5c5c,#b4b4b4)}
.tile-6{background:linear-gradient(135deg,#3c4b5c,#a3b6c6)}
.view-details{position:absolute;left:50%;top:50%;transform:translate(-50%,-50%);border:1px solid rgba(255,255,255,.7);color:var(--white);font-size:11px;padding:12px 24px;letter-spacing:.3px;text-transform:uppercase}

/* clients */
.clients{top:2850px;height:291px;background:var(--white)}
.clients .section-title{top:64px;color:var(--green)}
.clients .lead{top:104px;width:100%;text-align:center;font-size:12px;line-height:1.6;color:var(--muted)}
.client{top:184px;height:56px;display:flex;align-items:center;justify-content:center;gap:10px;font-size:30px;font-weight:600;color:#444}
.client-square{width:18px;height:18px;background:#444}

/* footer */
.site-footer{top:3141px;height:102px;background:var(--charcoal)}
.footer-nav{left:180px;top:30px;display:flex;gap:24px;font-size:11px;font-weight:600;color:var(--white);text-transform:uppercase}
.copyright{left:180px;top:54px;font-size:11px;color:#cfcfcf}
.social{left:896px;top:36px;display:flex;gap:6px}
.social span{width:25px;height:25px;border-radius:50%;background:var(--white)}
</style>
</head>
<body>

<header class="site-header">
  <div class="abs logo"><span class="logo-mark"></span>lorentavo</div>
  <nav class="abs main-nav">
    <span class="active">lorentavo</span><span>Services</span><span>Work</span><span>Credentials</span><span>Contact</span>
  </nav>
</header>

<section class="hero">
  <div class="abs hero-photo" role="img" aria-label="Businessman in a hard hat drawing a glowing city sketch on a chalkboard"></div>
  <div class="abs hero-box">
    <h1>Measuring and managing an employer brand</h1>
    <p>one key strategic tool for companies and their competitiveness A strong brand has a direct impact on the company's success (Halden, Moro, &amp; Petz, 2003).</p>
  </div>
</section>

<section class="welcome">
  <h2 class="abs section-title">Welcome to lorentavo</h2>
  <p class="abs lead">lorentavo ltd., a spin-off company from the University of Velmora, specializes in<br>empirical brand consulting:</p>
  <div class="abs divider"></div>
  <ul class="checklist">
    <li style="left:210px;top:165px"><svg width="14" height="12" viewBox="0 0 14 12"><path d="M1 6l4 4 8-9" fill="none" stroke="#222" stroke-width="2.4"/></svg>Testing your brand using scientifically developed tools.</li>
    <li style="left:210px;top:224px"><svg width="14" height="12" viewBox="0 0 14 12"><path d="M1 6l4 4 8-9" fill="none" stroke="#222" stroke-width="2.4"/></svg>Generating long-term effects thanks to a modeling and calculation of your brand success.</li>
    <li style="left:210px;top:295px"><svg width="14" height="12" viewBox="0 0 14 12"><path d="M1 6l4 4 8-9" fill="none" stroke="#222" stroke-width="2.4"/></svg>Cost optimization of your marketing and communication budgets by as much<br>as 30%.</li>
    <li style="left:627px;top:165px"><svg width="14" height="12" viewBox="0 0 14 12"><path d="M1 6l4 4 8-9" fill="none" stroke="#222" stroke-width="2.4"/></svg>Detailed examination of your marketing and communication procedures.</li>
    <li style="left:627px;top:224px"><svg width="14" height="12" viewBox="0 0 14 12"><path d="M1 6l4 4 8-9" fill="none" stroke="#222" stroke-width="2.4"/></svg>Development and implementation of strategies for your whole company, your products/services as well as for your CEO.</li>
  </ul>
</section>

<section class="services dark">
  <h2 class="abs section-title">lorentavo</h2>
  <p class="abs lead">Using our unique, scientifically tested instruments, lorentavo measures and<br>models your brand, so you can effectively and successfully manage it:</p>
  <article class="abs service-card" style="left:180px">
    <h3>Company brand</h3>
    <div class="card-photo" role="img" aria-label="Businessman drawing a rising chart on a wall"></div>
    <p>Sed ut perspiciatis unde omnis iste natus error sit voluptatem accusantium doloremque laudantium, totam rem aperiam.</p>
  </article>
  <article class="abs service-card" style="left:471px">
    <h3>Product/ service</h3>
    <div class="card-photo" role="img" aria-label="Businessman facing chalk-drawn stairs"></div>
    <p>Sed ut perspiciatis unde omnis iste natus error sit voluptatem accusantium doloremque laudantium, totam rem aperiam.</p>
  </article>
  <article class="abs service-card" style="left:761px">
    <h3>CEO brand</h3>
    <div class="card-photo" style="background:linear-gradient(180deg,#a9c8e0,#4f6e8c)" role="img" aria-label="Executives shaking hands in an office"></div>
    <p>Sed ut perspiciatis unde omnis iste natus error sit voluptatem accusantium doloremque laudantium, totam rem aperiam.</p>
  </article>
</section>

<section class="benefits">
  <h2 class="abs section-title">Our benefits</h2>
  <p class="abs lead">Sustainably increase your brand equity, and subsequently your company's success, through<br>more effective and efficient marketing &amp; communication activities:</p>

  <div class="abs benefit" style="left:155px;top:181px">
    <div class="badge"><svg width="60" height="56" viewBox="0 0 60 56" fill="#fff"><rect x="4" y="4" width="4" height="48"/><rect x="4" y="48" width="52" height="4"/><rect x="14" y="14" width="9" height="34"/><rect x="27" y="26" width="9" height="22"/><rect x="40" y="36" width="9" height="12"/></svg></div>
    <h4>Metrics</h4><p>You receive precise data for your brand perception of your target groups.</p>
  </div>
  <div class="abs benefit" style="left:386px;top:181px">
    <div class="badge"><svg width="64" height="56" viewBox="0 0 64 56"><rect x="4" y="4" width="56" height="38" fill="none" stroke="#fff" stroke-width="4"/><path d="M12 32l10-10 8 6 8-12 8 6 8-8" fill="none" stroke="#fff" stroke-width="3"/><rect x="28" y="42" width="8" height="8" fill="#fff"/><rect x="18" y="50" width="28" height="4" fill="#fff"/></svg></div>
    <h4>Trend models</h4><p>Thanks to our solid trend modeling, you manage your brand...</p>
  </div>
  <div class="abs benefit" style="left:618px;top:181px">
    <div class="badge"><svg width="70" height="46" viewBox="0 0 70 46" fill="#fff"><circle cx="16" cy="12" r="7"/><circle cx="54" cy="12" r="7"/><circle cx="35" cy="10" r="9"/><path d="M4 40c0-10 5-16 12-16s12 6 12 16z"/><path d="M42 40c0-10 5-16 12-16s12 6 12 16z"/><path d="M20 44c0-14 6-22 15-22s15 8 15 22z"/></svg></div>
    <h4>Precision</h4><p>You are better able to reach your customers. You can better...</p>
  </div>
  <div class="abs benefit" style="left:853px;top:181px">
    <div class="badge"><svg width="60" height="56" viewBox="0 0 60 56" fill="#fff"><ellipse cx="22" cy="44" rx="18" ry="6"/><ellipse cx="22" cy="35" rx="18" ry="6"/><ellipse cx="22" cy="26" rx="18" ry="6"/><ellipse cx="42" cy="40" rx="16" ry="5"/><ellipse cx="42" cy="32" rx="16" ry="5"/><ellipse cx="38" cy="16" rx="16" ry="6"/><ellipse cx="38" cy="8" rx="16" ry="6"/></svg></div>
    <h4>Cost reduction</h4><p>By using a more precise mix of communication, you are able to...</p>
  </div>

  <div class="abs benefit" style="left:155px;top:499px">
    <div class="badge"><svg width="68" height="46" viewBox="0 0 68 46" fill="none" stroke="#fff" stroke-width="4" stroke-linejoin="round"><path d="M2 14l12-8 14 6 10-4 12 4 16-8"/><path d="M14 6l-10 20"/><path d="M54 4l10 20"/><path d="M14 26l14 14 8-4 8 4 10-12"/><path d="M28 12l-4 10 8 2 6-6 10 10"/></svg></div>
    <h4>Closeness</h4><p>valuquant® lets you get even closer to your target groups.</p>
  </div>
  <div class="abs benefit" style="left:386px;top:499px">
    <div class="badge"><svg width="50" height="60" viewBox="0 0 50 60" fill="none" stroke="#fff" stroke-width="4"><path d="M12 26V16a13 13 0 0 1 26 0"/><rect x="5" y="26" width="40" height="30"/><circle cx="25" cy="40" r="5"/></svg></div>
    <h4>Security</h4><p>valuquant® makes opinions and attitudes immediately visual.</p>
  </div>
  <div class="abs benefit" style="left:618px;top:499px">
    <div class="badge"><svg width="64" height="50" viewBox="0 0 64 50"><rect x="3" y="3" width="58" height="44" fill="none" stroke="#fff" stroke-width="4"/><rect x="10" y="12" width="16" height="18" fill="#fff"/><rect x="32" y="14" width="22" height="3" fill="#fff"/><rect x="32" y="22" width="22" height="3" fill="#fff"/><rect x="10" y="36" width="44" height="3" fill="#fff"/></svg></div>
    <h4>Fit</h4><p>valuquant® allows a custom-fit communication with your target groups.</p>
  </div>
  <div class="abs benefit" style="left:853px;top:499px">
    <div class="badge"><svg width="70" height="56" viewBox="0 0 70 56"><path d="M6 30l20 20L64 8" fill="none" stroke="#fff" stroke-width="11"/></svg></div>
    <h4>Customer loyalty/<br>acquisition</h4><p>valuquant® supports the bond to</p>
  </div>
</section>

<section class="press dark">
  <h2 class="abs section-title">Press release</h2>
  <p class="abs lead">Using our unique, scientifically tested instruments, lorentavo measures and<br>models your brand, so you can effectively and successfully manage it:</p>
  <div class="abs press-grid">
    <div class="press-tile tile-1" role="img" aria-label="Blue arrow rising over a surface"></div>
    <div class="press-tile tile-2" role="img" aria-label="Financial charts on a screen"><span class="view-details">View details</span></div>
    <div class="press-tile tile-3" role="img" aria-label="Glowing data graphs"></div>
    <div class="press-tile tile-4" role="img" aria-label="Hand with pen over printed charts"></div>
    <div class="press-tile tile-5" role="img" aria-label="Person pointing at stock charts on glass"></div>
    <div class="press-tile tile-6" role="img" aria-label="Businessman drawing a growth curve"></div>
  </div>
</section>

<section class="clients">
  <h2 class="abs section-title">Our clients</h2>
  <p class="abs lead">We are based on our experience, our knowledge and our science based approach, the specialists in the<br>empirical brand consultancy</p>
  <div class="abs client" style="left:180px;width:144px">Ostrel</div>
  <div class="abs client" style="left:374px;width:138px;font-size:26px">Paveno</div>
  <div class="abs client" style="left:580px;width:265px;font-size:26px">Lumbrakt</div>
  <div class="abs client" style="left:876px;width:142px;font-size:26px"><span class="client-square"></span>tz.ch</div>
</section>

<footer class="site-footer">
  <nav class="abs footer-nav"><span>lorentavo</span><span>Services</span><span>Work</span><span>Credentials</span><span>Contact</span></nav>
  <p class="abs copyright">© 2014 lorentavo.ch. All rights reserved.</p>
  <div class="abs social" aria-label="Social links"><span></span><span></span><span></span><span></span></div>
</footer>

</body>
</html>
```